Beverage Social Media Illustration. Logo and fruit splashing in water

Hello! We are looking for a graphic design to be used for facebook / instagram posts to promote a local event in Santa Monica, CA

We are a healthy lifestyle/protein-based food and beverage company. This is for our Protein Water line called HydraLeaf. All are under 100 calories, sugar, fat, carb and lactose free w 100% US-sourced non-GMO protein.

I would like to feature our logo in front, perhaps floating on water. In the background I would like to have fruit pieces either splashing down into the water or splashing up out of the water. The fruit pieces are meant to represent the different flavors offerings. Our beverages are colored, so if it makes sense / looks good, perhaps the water effect under the pineapple could be yellow, etc.

My goal is to use the full image for something like a facebook or website cover photo. Then perhaps the logo with just one of the fruit pieces for a post or to represent the product. Once we have our full packaging for the US market done, we will include that. At this point, we are just taste testing.

Our launch flavors for the US are:
Pineapple Mint = yellow
Blueberry = blue
Acai berry = purple
Watermelon Lime = red
Tangerine = Orange

I'm pasting the elevator pitch for our company below. We are positioning ourselves as a lifestyle company. I've also included some concept artwork of what our packaging might look like for the US market. At this time we are just taste testing and finalizing our formulations. This is why I would like to stay away from featuring a bottle.

Thank you in advance for your consideration!

HydraLeaf is a food and beverage company that believes in protein as a healthy food, not just a weight-lifting supplement. We were founded on the basic principle that not all calories are created equal. If [you] are going to have 100 calories, 100 calories of protein is better than 100 calories of carbs or 100 calories of fat. That's it :)

Target Market(s)

We are positioning ourselves as a healthy lifestyle / protein food and beverage company. Think salad and an HydraLeaf for lunch more so than chugging it 30m after lifting a lot of weights.

Industry/Entity Type

Graphic Design

Font styles to use
Sans Serif

Colors
33a6d7
ec1f27
fbed22
0655a3
f78f20

Requirements
Must have
• Feature logo with Hydra Blue
Nice to have
• water from splash effect colored to match teh corresponding flavor
Should not have
• feature bottle design

```html
<!DOCTYPE html>
<html lang="en">
<head>
<meta charset="utf-8">
<title>HydraLeaf – Protein Water Flavours</title>
<link href="https://fonts.googleapis.com/css2?family=Fredoka:wght@600&display=swap" rel="stylesheet">
<style>
  :root {
    --hydra-blue: #33a6d7;
    --brand-light: #8fd3ec;
    --splash-light: #bfe6f5;
    --water-top: #52c2e6;
    --water-bottom: #66d3ee;
    --acai: #7a3fd0;
    --pineapple: #fbed22;
    --pineapple-flesh: #f4e27a;
    --watermelon: #ec1f27;
    --watermelon-flesh: #f2545a;
    --tangerine: #f78f20;
    --tangerine-flesh: #f9b25a;
    --blueberry: #33a6d7;
    --berry-skin: #2c3350;
    --paper: #ffffff;
  }
  * { margin: 0; padding: 0; box-sizing: border-box; }
  html, body {
    width: 1200px;
    height: 676px;
    overflow: hidden;
    background: var(--paper);
  }
  .cover {
    position: relative;
    width: 1200px;
    height: 676px;
    background: var(--paper);
    overflow: hidden;
  }
  .brand-name {
    position: absolute;
    top: 34px;
    left: 0;
    width: 100%;
    text-align: center;
    font-family: "Fredoka", sans-serif;
    font-weight: 600;
    font-size: 30px;
    line-height: 1;
    letter-spacing: 4px;
    color: var(--brand-light);
    z-index: 2;
  }
  .scene {
    position: absolute;
    inset: 0;
    width: 1200px;
    height: 676px;
  }
</style>
</head>
<body>
  <main class="cover">
    <h1 class="brand-name">HYDRALEAF</h1>

    <svg class="scene" viewBox="0 0 1200 676" xmlns="http://www.w3.org/2000/svg">
      <defs>
        <linearGradient id="flavour-band" x1="0" y1="0" x2="1" y2="0">
          <stop offset="0" stop-color="var(--acai)"/>
          <stop offset="0.14" stop-color="var(--acai)" stop-opacity="0.8"/>
          <stop offset="0.28" stop-color="var(--pineapple)"/>
          <stop offset="0.45" stop-color="var(--watermelon)"/>
          <stop offset="0.68" stop-color="var(--tangerine)"/>
          <stop offset="0.85" stop-color="var(--blueberry)" stop-opacity="0.8"/>
          <stop offset="1" stop-color="var(--blueberry)"/>
        </linearGradient>
        <linearGradient id="water-body" x1="0" y1="0" x2="0" y2="1">
          <stop offset="0" stop-color="var(--water-top)"/>
          <stop offset="1" stop-color="var(--water-bottom)"/>
        </linearGradient>
        <radialGradient id="splash-glow" cx="0.5" cy="0.5" r="0.5">
          <stop offset="0" stop-color="var(--splash-light)" stop-opacity="0.9"/>
          <stop offset="1" stop-color="var(--splash-light)" stop-opacity="0"/>
        </radialGradient>
        <filter id="soft-edge" x="-5%" y="-20%" width="110%" height="140%">
          <feGaussianBlur stdDeviation="4"/>
        </filter>
      </defs>

      <rect class="hero-splash" x="486" y="82" width="200" height="260" rx="60"
        fill="url(#splash-glow)" role="img"
        aria-label="Clear water splash rising from the surface behind the brand name"/>

      <g class="flavour-splash" role="img" aria-label="Coloured juice splashes for acai, pineapple mint, watermelon lime, tangerine and blueberry along the water surface">
        <path filter="url(#soft-edge)" fill="url(#flavour-band)" opacity="0.8"
          d="M0 375 C60 350 120 340 170 360 C230 330 290 330 340 350 C400 320 450 335 480 365
             C540 330 600 335 640 358 C700 330 760 338 800 365 C860 335 920 340 960 362
             C1030 340 1100 340 1150 355 C1175 345 1190 350 1200 355 L1200 470 L0 470 Z"/>
      </g>

      <path class="water" fill="url(#water-body)"
        d="M0 440 C80 420 160 445 240 430 C320 415 400 440 500 432 C600 424 680 445 780 432
           C880 420 960 438 1060 428 C1120 422 1170 430 1200 426 L1200 676 L0 676 Z"/>

      <g class="fruit acai-berries" role="img" aria-label="Acai berries and blueberries splashing on the left">
        <circle cx="62" cy="324" r="17" fill="var(--berry-skin)"/>
        <circle cx="174" cy="366" r="21" fill="var(--berry-skin)"/>
        <circle cx="82" cy="432" r="12" fill="var(--berry-skin)"/>
      </g>

      <rect class="fruit pineapple" x="330" y="340" width="80" height="115" rx="18"
        fill="var(--pineapple-flesh)" opacity="0.9" role="img"
        aria-label="Pineapple chunk in yellow splash"/>

      <rect class="fruit watermelon" x="528" y="378" width="92" height="100" rx="20"
        fill="var(--watermelon-flesh)" opacity="0.9" role="img"
        aria-label="Watermelon wedge in red splash"/>

      <ellipse class="fruit tangerine" cx="830" cy="418" rx="42" ry="50"
        fill="var(--tangerine-flesh)" opacity="0.9" role="img"
        aria-label="Tangerine segments in orange splash"/>

      <g class="fruit blueberries" role="img" aria-label="Blueberries splashing on the right">
        <circle cx="1144" cy="354" r="18" fill="var(--berry-skin)"/>
        <circle cx="1080" cy="378" r="14" fill="var(--berry-skin)"/>
        <circle cx="1098" cy="426" r="19" fill="var(--berry-skin)"/>
      </g>
    </svg>
  </main>
</body>
</html>
```